RW Holloway LLC Business Card - Civil Engineering & Consulting Firm

We need a Business Card that is elegant, and masculine.  It is our Professional Civil Engineering & Consulting Company located in San Antonio TX (Not s construction or builder firm- no gears & no tool images please). We provide civil engineering services including  commercial site plans, grading and drainage plans, utility plans, hydraulics and hydrology, land planning, utility coordination, and other general civil engineering services related to commercial and residential development.
We have 2 existing Logos. We would like to convey reliability, strength, trustworthiness and attention to detail.  Blues and orange tones as per logo We are OK with the use of a darker blue in the mix.  We have 2 logo versions - Full Company Name Logo to go on the back of card, & Small Icon Logo for the front w/ personal Info.

Target Market(s)
Architects, Real Estate Developers, Other Strctural Engineers, Surveyers, General Contractors
Industry/Entity Type
Professional Civil Engineering
Contact Information for Business Card
Name, Position, Address, Cell & Office #, email, and company website
Font styles to use
Other font styles liked:
- Avian
Requirements
Should not have
- No Tools, No Gears, no Cranes, or Construction Equipment.

```html
<!DOCTYPE html>
<html lang="en">
<head>
<meta charset="utf-8">
<title>RW Holloway LLC – Business Card</title>
<link rel="stylesheet" href="https://fonts.googleapis.com/css2?family=Montserrat:wght@400;500;700&display=swap">
<style>
  :root {
    --stage: #b9b9b9;
    --card-white: #f4f3f4;
    --facet-light: #ffffff;
    --facet-dark: #e2e1e3;
    --orange: #ef8d27;
    --blue: #74a4d6;
    --steel: #7f9fbd;
    --back-orange: #e0934a;
    --ink: #1c1c1c;
    --white: #ffffff;
  }
  * { box-sizing: border-box; margin: 0; padding: 0; }
  html, body { width: 1200px; height: 813px; overflow: hidden; }
  body {
    background: var(--stage);
    font-family: "Montserrat", Arial, sans-serif;
    display: flex;
    align-items: center;
    justify-content: center;
    gap: 40px;
  }
  .card {
    position: relative;
    width: 560px;
    height: 320px;
    overflow: hidden;
    box-shadow: 0 12px 28px rgba(0,0,0,.35);
  }
  .card .facets { position: absolute; inset: 0; width: 100%; height: 100%; }

  /* Front */
  .card-front { background: var(--card-white); color: var(--ink); }
  .brand {
    position: absolute; left: 40px; top: 44px;
    display: flex; align-items: center; gap: 10px;
    font-weight: 700; font-size: 20px; color: var(--orange);
  }
  .brand-square { width: 16px; height: 16px; background: var(--blue); }
  .person { position: absolute; left: 40px; top: 150px; }
  .person-name {
    font-weight: 700; font-size: 22px; letter-spacing: .5px;
    color: var(--orange); text-transform: uppercase;
  }
  .person-role { font-size: 15px; margin-top: 6px; }
  .divider {
    position: absolute; left: 292px; top: 112px;
    width: 2px; height: 110px; background: var(--orange);
  }
  .contacts {
    position: absolute; left: 312px; top: 110px;
    list-style: none; font-size: 14px; font-weight: 500;
  }
  .contacts li { display: flex; align-items: center; gap: 10px; height: 28px; }
  .contacts svg { width: 16px; height: 16px; fill: var(--orange); flex: none; }
  .address {
    position: absolute; left: 40px; bottom: 36px;
    font-size: 14px; font-weight: 500;
  }

  /* Back */
  .card-back {
    background: linear-gradient(200deg, var(--steel) 0%, #a59e98 45%, var(--back-orange) 100%);
    color: var(--white);
  }
  .back-name {
    position: absolute; inset: 0;
    display: flex; align-items: center; justify-content: center;
    font-weight: 400; font-size: 38px; letter-spacing: 3px;
    text-transform: uppercase; color: var(--white);
  }
</style>
</head>
<body>

  <section class="card card-front">
    <svg class="facets" viewBox="0 0 560 320" preserveAspectRatio="none" aria-hidden="true">
      <polygon points="0,0 200,0 120,320 0,320" fill="var(--facet-dark)" opacity=".5"/>
      <polygon points="200,0 560,0 560,110 330,320 120,320" fill="var(--facet-light)" opacity=".45"/>
      <polygon points="0,200 300,140 560,230 560,320 0,320" fill="var(--facet-dark)" opacity=".35"/>
    </svg>

    <div class="brand"><span class="brand-square"></span>RW Holloway LLC</div>

    <div class="person">
      <p class="person-name">Dana Whitfield</p>
      <p class="person-role">Co-Founder</p>
    </div>

    <div class="divider"></div>

    <ul class="contacts">
      <li>
        <svg viewBox="0 0 24 24" aria-hidden="true"><path d="M6.6 10.8a15 15 0 0 0 6.6 6.6l2.2-2.2a1 1 0 0 1 1-.25 11.4 11.4 0 0 0 3.6.57 1 1 0 0 1 1 1V20a1 1 0 0 1-1 1A17 17 0 0 1 3 4a1 1 0 0 1 1-1h3.5a1 1 0 0 1 1 1c0 1.25.2 2.45.57 3.57a1 1 0 0 1-.25 1z"/></svg>
        555-014-2290
      </li>
      <li>
        <svg viewBox="0 0 24 24" aria-hidden="true"><path d="M3 6c3-3 15-3 18 0v3h-4V7.5c-2-1-8-1-10 0V9H3zM7 10h10l3 9H4zm5 2.5a2.5 2.5 0 1 0 0 5 2.5 2.5 0 0 0 0-5z"/></svg>
        555-014-3174
      </li>
      <li>
        <svg viewBox="0 0 24 24" aria-hidden="true"><path d="M2 5h20v14H2zm2 2v.5l8 5.5 8-5.5V7l-8 5z"/></svg>
        info@rwholloway
      </li>
      <li>
        <svg viewBox="0 0 24 24" aria-hidden="true"><path d="M12 2a10 10 0 1 0 0 20 10 10 0 0 0 0-20zm-1 17.9A8 8 0 0 1 4.1 11H7c.1 3.3 1.5 6.5 4 8.9zM4.1 9A8 8 0 0 1 11 4.1C8.5 6.5 7.1 9 7 9zm8.9 10.9c2.5-2.4 3.9-5.6 4-8.9h2.9a8 8 0 0 1-6.9 8.9zM17 9c-.1-.1-1.5-2.5-4-4.9A8 8 0 0 1 19.9 9zM9 11h6c-.1 2.7-1.2 5.3-3 7.3-1.8-2-2.9-4.6-3-7.3zm0-2c.3-2 1.3-4 3-5.5 1.7 1.5 2.7 3.5 3 5.5z"/></svg>
        www.hollowayeng.com
      </li>
    </ul>

    <p class="address">4180 Alder Creek Road Suite 210 Marlow 28</p>
  </section>

  <section class="card card-back">
    <svg class="facets" viewBox="0 0 560 320" preserveAspectRatio="none" aria-hidden="true">
      <polygon points="0,0 260,0 120,320 0,320" fill="var(--facet-light)" opacity=".08"/>
      <polygon points="330,0 560,0 560,170" fill="var(--facet-light)" opacity=".1"/>
      <polygon points="260,320 560,200 560,320" fill="var(--back-orange)" opacity=".35"/>
    </svg>
    <div class="back-name">RW Holloway LLC</div>
  </section>

</body>
</html>
```